Website for Apartment Rental in Prague

I would like to create designs of my website focused on luxury apartment rentals in Prague, Czech Republic. I created initial mock-ups, They are all attached. I need to design homepage and subpage. The mock-ups were created by combining elements from different websites that I liked but I need you to create a design that is unique and original. The attached files a only a guidance for the structure of the website but not for the design. Try to be creative.

Apartment

```html
<!DOCTYPE html>
<html lang="en">
<head>
<meta charset="utf-8">
<title>Maison Lumen Apartments Prague</title>
<link href="https://fonts.googleapis.com/css2?family=Cinzel:wght@400&family=Cormorant+SC:wght@500&family=Lato:ital,wght@0,400;0,700;1,400&display=swap" rel="stylesheet">
<style>
:root{
  --navy:#333b48;
  --navy-deep:#2b323d;
  --sand:#b5a28b;
  --gold:#a8977d;
  --ink:#2b2b2b;
  --muted:#555;
  --paper:#ffffff;
  --mist:#ececec;
  --line:#d8d8d8;
}
*{box-sizing:border-box;margin:0;padding:0}
html,body{width:1200px;height:2244px;overflow:hidden}
body{font-family:"Lato",Arial,sans-serif;color:var(--ink);background:var(--paper);position:relative}
.abs{position:absolute}

/* top bar */
.topbar{position:absolute;top:0;left:0;width:1200px;height:54px;background:var(--navy);color:#fff;font-size:13px}
.topbar .item{position:absolute;top:12px;display:flex;align-items:center;gap:10px;height:30px}
.round-icon{width:30px;height:30px;border-radius:50%;background:#d9d2c6;display:flex;align-items:center;justify-content:center}
.lang{border:1px solid #fff;padding:1px 5px;font-size:12px;margin-left:14px}

/* nav */
.nav{position:absolute;top:54px;left:0;width:1200px;height:51px;background:var(--paper)}
.nav a{position:absolute;top:19px;font-size:10px;letter-spacing:1.2px;color:var(--ink);text-decoration:none;text-transform:uppercase;white-space:nowrap}
.nav a.tight{letter-spacing:.8px}
.nav a.plain{font-size:13px;letter-spacing:.5px;top:16px}
.brand-tab{position:absolute;top:54px;left:0;width:1200px;height:76px;z-index:3;pointer-events:none}
.brand-name{position:absolute;top:68px;left:500px;width:200px;text-align:center;font-family:"Cinzel",serif;font-size:26px;color:var(--gold);z-index:4;line-height:1.1}

/* hero */
.hero{position:absolute;top:105px;left:0;width:1200px;height:505px;background:linear-gradient(160deg,#6b5a47 0%,#b79f84 35%,#d8cbb8 55%,#8d7c6b 80%,#5a4a3e 100%)}
.hero-title{position:absolute;top:328px;left:450px;width:340px;height:50px;background:rgba(60,55,50,.45);color:#fff;font-size:26px;letter-spacing:1.5px;display:flex;align-items:center;justify-content:center;font-weight:700}
.hero-arrow{position:absolute;top:280px;width:46px;height:98px}

/* booking */
.booking{position:absolute;top:610px;left:0;width:1200px;height:171px;background:var(--navy);color:#fff}
.booking h2{position:absolute;top:27px;width:100%;text-align:center;font-size:19px;font-weight:700;letter-spacing:.4px}
.field{position:absolute;top:65px;height:26px;background:#fff;color:#777;font-size:12px;font-style:italic;padding:5px 9px;display:flex;justify-content:space-between;align-items:center}
.btn{display:inline-flex;align-items:center;justify-content:center;color:#fff;font-size:12.5px;font-weight:700;text-transform:uppercase;letter-spacing:.3px}
.btn-sand{background:var(--sand)}
.btn-navy{background:var(--navy)}
.booking .btn{position:absolute;top:111px;height:30px}

/* section headings */
.section-title{position:absolute;width:100%;text-align:center;font-family:"Cormorant SC",serif;font-weight:500;font-size:32px;letter-spacing:2.5px;color:var(--ink)}
.section-title span{color:var(--gold)}
.divider{position:absolute;left:525px;width:150px;height:14px}
.intro-text{position:absolute;top:897px;left:135px;width:930px;text-align:center;font-size:13.5px;line-height:21px;color:var(--ink)}

/* listings */
.listings{position:absolute;top:1044px;left:0;width:1200px;height:793px;background:var(--mist)}
.card{position:absolute;width:289px;height:321px;background:var(--paper)}
.card .photo{position:absolute;top:0;left:0;width:289px;height:154px}
.price{position:absolute;top:112px;left:0;background:var(--navy);color:#fff;font-size:12.5px;font-weight:700;padding:7px 10px}
.card h3{position:absolute;top:166px;left:10px;right:4px;font-family:"Cinzel",serif;font-weight:400;font-size:12px;line-height:16px;color:var(--gold);letter-spacing:.2px}
.card .meta{position:absolute;top:211px;left:10px;font-size:12.5px;color:var(--ink)}
.card .meta b{font-weight:700}
.card .desc{position:absolute;top:237px;left:10px;right:12px;font-size:11.5px;line-height:15px;color:var(--ink)}
.card .btn{position:absolute;top:273px;height:26px}
.card .btn.details{left:10px;width:100px}
.card .btn.book{left:121px;width:100px}

.know{position:absolute;left:769px;top:1463px;width:289px;height:321px;background:var(--paper)}
.know h3{position:absolute;top:18px;left:20px;font-family:"Cormorant SC",serif;font-weight:500;font-size:25px;letter-spacing:2px;color:var(--ink)}
.know .divider{left:90px;top:62px;width:110px}
.know-item{position:absolute;left:20px;width:260px;display:flex;gap:10px}
.know-item .ic{flex:none;width:42px;height:42px;border-radius:50%;background:var(--sand);display:flex;align-items:center;justify-content:center}
.know-item h4{font-size:12.5px;color:var(--gold);text-transform:uppercase;font-weight:700;margin-top:2px}
.know-item p{font-size:11px;line-height:14px;color:var(--ink);margin-top:3px}

/* reviews */
.review-sub{position:absolute;top:1968px;width:100%;text-align:center;font-size:13px;letter-spacing:1.8px;color:var(--gold);font-weight:700;text-transform:uppercase}
.review-badge{position:absolute;top:1995px;left:571px;width:58px;height:58px;border-radius:50%;border:1.5px solid var(--gold);display:flex;align-items:center;justify-content:center}
.review-text{position:absolute;top:2059px;left:135px;width:930px;text-align:center;font-size:13px;line-height:21px}
.review-arrow{position:absolute;top:2082px;width:16px;height:26px}

/* footer */
.footer{position:absolute;top:2199px;left:0;width:1200px;height:45px;background:var(--navy);color:#fff;font-size:11px}
.footer .copy{position:absolute;top:17px;left:143px}
.social{position:absolute;top:11px;left:546px;display:flex;gap:8px}
.social span{width:22px;height:22px;border-radius:50%;background:#fff;border:3px solid #5b7fbf}
.social span:nth-child(2){border-color:#3ba3e0}
.social span:nth-child(3){border-color:#2a6fa8}
.social span:nth-child(4){border-color:#c7312b}
.message{position:absolute;top:2196px;left:838px;width:220px;height:48px;background:var(--sand);color:#fff;font-size:14px;display:flex;align-items:center;gap:12px;padding-left:14px}
</style>
</head>
<body>

<header class="topbar">
  <div class="item" style="left:140px">
    <span class="round-icon"><svg width="16" height="16" viewBox="0 0 16 16"><circle cx="8" cy="5" r="3" fill="#333b48"/><path d="M2 15c0-4 3-6 6-6s6 2 6 6z" fill="#333b48"/></svg></span>
    <span>OUR HOPITALITY</span>
    <span class="lang">EN ▾</span>
  </div>
  <div class="item" style="left:680px">
    <span class="round-icon"><svg width="16" height="16" viewBox="0 0 16 16"><path d="M4 1l3 3-2 2c1 2 3 4 5 5l2-2 3 3-2 3C7 14 2 9 1 4z" fill="#333b48"/></svg></span>
    <span>+420 600 418 233</span>
  </div>
  <div class="item" style="left:838px">
    <span class="round-icon"><svg width="16" height="12" viewBox="0 0 16 12"><rect x="0.5" y="0.5" width="15" height="11" fill="none" stroke="#333b48"/><path d="M1 1l7 6 7-6" fill="none" stroke="#333b48"/></svg></span>
    <span>booking@lumenstays.com</span>
  </div>
</header>

<nav class="nav">
  <a href="#" style="left:145px">Apartments</a>
  <a href="#" style="left:251px">Location</a>
  <a href="#" class="plain" style="left:336px">SERVICES</a>
  <a href="#" style="left:421px">Gallery</a>
  <a href="#" class="tight" style="left:704px">Exclusive Offers . Tours</a>
  <a href="#" class="tight" style="left:883px">For Families</a>
  <a href="#" class="tight" style="left:982px">Contact Us</a>
</nav>
<svg class="brand-tab" viewBox="0 0 1200 76" aria-hidden="true"><path d="M500 50 Q600 88 698 50 L698 0 L500 0 Z" fill="#fff"/></svg>
<div class="brand-name">Maison<br>Lumen</div>

<section class="hero" role="img" aria-label="Photo of a bright open-plan luxury apartment living room with sofas and a glass chandelier">
  <div class="hero-title">BEING HOME IN PRAGUE</div>
  <svg class="hero-arrow" style="left:0" viewBox="0 0 46 98"><path d="M0 0 L46 49 L0 98 Z" fill="#fff" opacity=".9"/><path d="M20 40 l-8 9 8 9" stroke="#333b48" stroke-width="3" fill="none"/></svg>
  <svg class="hero-arrow" style="right:0" viewBox="0 0 46 98"><path d="M46 0 L0 49 L46 98 Z" fill="#fff" opacity=".9"/><path d="M26 40 l8 9 -8 9" stroke="#333b48" stroke-width="3" fill="none"/></svg>
</section>

<section class="booking">
  <h2>OFFICIAL SITE &nbsp;-&nbsp; BEST PRICE GUARANTEED</h2>
  <div class="field" style="left:142px;width:146px">Check in date <svg width="14" height="13" viewBox="0 0 14 13"><rect x=".5" y="1.5" width="13" height="11" fill="none" stroke="#bbb"/><path d="M1 5h12" stroke="#bbb"/></svg></div>
  <div class="field" style="left:298px;width:146px">Check out date <svg width="14" height="13" viewBox="0 0 14 13"><rect x=".5" y="1.5" width="13" height="11" fill="none" stroke="#bbb"/><path d="M1 5h12" stroke="#bbb"/></svg></div>
  <div class="field" style="left:455px;width:95px">Adults <svg width="10" height="6"><path d="M0 0h10L5 6z" fill="#777"/></svg></div>
  <div class="field" style="left:562px;width:115px">Children <svg width="10" height="6"><path d="M0 0h10L5 6z" fill="#777"/></svg></div>
  <div class="field" style="left:689px;width:95px">Infants <svg width="10" height="6"><path d="M0 0h10L5 6z" fill="#777"/></svg></div>
  <div class="field" style="left:796px;width:263px">Promotional Code</div>
  <span class="btn btn-sand" style="left:413px;width:162px">Check Availibility</span>
  <span class="abs" style="left:583px;top:118px;font-size:13px">Or</span>
  <span class="btn btn-sand" style="left:605px;width:182px;justify-content:flex-start;padding-left:16px">Select Rental Unit<span style="position:absolute;right:0;top:0;width:26px;height:30px;border-left:1px solid #fff;display:flex;align-items:center;justify-content:center"><svg width="10" height="6"><path d="M0 0h10L5 6z" fill="#fff"/></svg></span></span>
</section>

<section>
  <h2 class="section-title" style="top:830px">A DIFFERENT VISION <span>OF TRAVELLING</span></h2>
  <svg class="divider" style="top:874px" viewBox="0 0 150 14"><path d="M0 7h64M86 7h64" stroke="#ccc" stroke-dasharray="2 2"/><circle cx="75" cy="7" r="6" fill="#ddd"/><circle cx="75" cy="7" r="3" fill="#aaa"/></svg>
  <p class="intro-text">Something spectacular has arrived in the heart of Europe. Steps from Old Town, this rental experience is curated with world-class amenities, exemplary style and a level of convenience you have to experience to believe. Experience the different vision of luxury in center of Prague.</p>
  <span class="btn btn-navy abs" style="top:959px;left:553px;width:95px;height:30px">Read More</span>
</section>

<section class="listings" aria-label="Apartments"></section>

<article class="card" style="left:142px;top:1107px">
  <div class="photo" role="img" aria-label="Photo of a contemporary living room with a wall-mounted screen" style="background:linear-gradient(135deg,#4a3e33,#a89680 55%,#d9cdbd)"></div>
  <span class="price">FROM 150 USD</span>
  <h3>BRAND NEW LUXURY LIVING SHINNING CONTEMPORARY DESIGN</h3>
  <p class="meta"><b>Bedroom : 1 &nbsp; People : max 4</b></p>
  <p class="desc">The 22nd issue is dedicated to colors...</p>
  <span class="btn btn-navy details">Details</span><span class="btn btn-sand book">Book Now</span>
</article>
<article class="card" style="left:455px;top:1107px">
  <div class="photo" role="img" aria-label="Photo of a white lounge with floor-to-ceiling windows over the city" style="background:linear-gradient(180deg,#8fa6bf,#d7dde2 50%,#6b6661)"></div>
  <span class="price">FROM 150 USD</span>
  <h3>BRAND NEW ZEN LUXURY LIVING<br>APARTMENT IN THE CENTER OF PRAGUE</h3>
  <p class="meta"><b>Bedroom : 1 &nbsp; People : max 4</b></p>
  <p class="desc">Recognized with Wanderline Journal 2017 Readers' Choice Award #1 hotel in the world</p>
  <span class="btn btn-navy details">Details</span><span class="btn btn-sand book">Book Now</span>
</article>
<article class="card" style="left:769px;top:1107px">
  <div class="photo" role="img" aria-label="Photo of a rooftop terrace lounge with city skyline" style="background:linear-gradient(180deg,#7fa8cf,#c9dbe8 45%,#8b8a6a 75%,#5d5c45)"></div>
  <span class="price">FROM 150 USD</span>
  <h3>EXPEDITION PRAGUE! TOP LOCA'<br>BRAND NEW APARTMENT</h3>
  <p class="meta"><b>Bedroom : 1 &nbsp; People : max 4</b></p>
  <p class="desc">For your Management committee,showroom session. Incentive trip. product launch. privatization...</p>
  <span class="btn btn-navy details">Details</span><span class="btn btn-sand book">Book Now</span>
</article>
<article class="card" style="left:142px;top:1463px">
  <div class="photo" role="img" aria-label="Photo of a penthouse bedroom with warm lighting" style="background:linear-gradient(135deg,#3a3530,#8a7a68 50%,#d6c8b6)"></div>
  <span class="price">FROM 150 USD</span>
  <h3>BRAND NEW SUNNY PENTHOUSE<br>WITH A VIEW OF PRAGUE</h3>
  <p class="meta"><b>Studio &nbsp; People : max 4</b></p>
  <p class="desc">The 22nd issue is dedicated to colors...</p>
  <span class="btn btn-navy details">Details</span><span class="btn btn-sand book">Book Now</span>
</article>
<article class="card" style="left:455px;top:1463px">
  <div class="photo" role="img" aria-label="Photo of a modern apartment building with a pool at dusk" style="background:linear-gradient(180deg,#2f4566,#6e7d96 45%,#c49a6c 70%,#3b3d44)"></div>
  <span class="price">FROM 150 USD</span>
  <h3>BRAND NEW MODERN APARTMENT<br>UNBEATABLE 1.0 CAT EON</h3>
  <p class="meta"><b>Bedroom : 1 &nbsp; People : max 4</b></p>
  <p class="desc">Recognized with Wanderline Journal 2017 Readers' Choice Award #1 hotel in the world</p>
  <span class="btn btn-navy details">Details</span><span class="btn btn-sand book">Book Now</span>
</article>

<aside class="know">
  <h3>NEED TO KNOW</h3>
  <svg class="divider" viewBox="0 0 110 14"><path d="M0 7h46M64 7h46" stroke="#ccc" stroke-dasharray="2 2"/><circle cx="55" cy="7" r="6" fill="#ddd"/><circle cx="55" cy="7" r="3" fill="#aaa"/></svg>
  <div class="know-item" style="top:84px">
    <span class="ic"><svg width="18" height="22" viewBox="0 0 18 22"><rect x="1" y="1" width="16" height="20" fill="none" stroke="#fff" stroke-width="1.5"/><path d="M5 5h2M11 5h2M5 9h2M11 9h2M5 13h2M11 13h2" stroke="#fff" stroke-width="2"/></svg></span>
    <div><h4>Aparments</h4><p>also available to rent all the apartments together for companies or larger groups,</p></div>
  </div>
  <div class="know-item" style="top:162px">
    <span class="ic"><svg width="18" height="22" viewBox="0 0 18 22"><rect x="3" y="1" width="12" height="20" fill="none" stroke="#fff" stroke-width="1.5"/><path d="M1 11h8M6 8l3 3-3 3" stroke="#fff" stroke-width="1.5" fill="none"/></svg></span>
    <div><h4>Check-Out</h4><p>12 noon; earliest check-in, 3pm - both are flexible, by arrangement.</p></div>
  </div>
  <div class="know-item" style="top:234px">
    <span class="ic"><svg width="22" height="22" viewBox="0 0 22 22"><circle cx="11" cy="11" r="9" fill="none" stroke="#fff" stroke-width="1.5"/><path d="M14 7.5c-1-1-5-1.5-5 1s5 1.5 5 4-4 2-5 1M11 5v12" stroke="#fff" stroke-width="1.5" fill="none"/></svg></span>
    <div><h4>Rates</h4><p>prices from 150 USD per night, including tax</p></div>
  </div>
</aside>

<section aria-label="Customer reviews">
  <h2 class="section-title" style="top:1885px">CUSTOMER <span>REVIEWS</span></h2>
  <svg class="divider" style="top:1929px" viewBox="0 0 150 14"><path d="M0 7h64M86 7h64" stroke="#ccc" stroke-dasharray="2 2"/><circle cx="75" cy="7" r="6" fill="#ddd"/><circle cx="75" cy="7" r="3" fill="#aaa"/></svg>
  <p class="review-sub">Interiors designed by Maison Lumen</p>
  <div class="review-badge"><svg width="30" height="28" viewBox="0 0 30 28"><path d="M2 13L15 2l13 11M6 10v16h18V10" fill="none" stroke="#a8977d" stroke-width="2.5"/><rect x="10" y="15" width="10" height="7" fill="#a8977d"/></svg></div>
  <p class="review-text">Maison Lumen offers short term and as well as long term options in our studio apartments and our one bedroom apartment homes. Our luxurious apartments and high quality customer service have allowed us to dominate the Prague apartment market with a proven track record. Our years of experience and knowledge have made us a premier apartment rental company as we continue to stress the importance of servicing individuals and corporations who are seeking the finest accommodations.</p>
  <svg class="review-arrow" style="left:98px" viewBox="0 0 16 26"><path d="M13 2L3 13l10 11" stroke="#bbb" stroke-width="2.5" fill="none"/></svg>
  <svg class="review-arrow" style="left:1080px" viewBox="0 0 16 26"><path d="M3 2l10 11L3 24" stroke="#bbb" stroke-width="2.5" fill="none"/></svg>
</section>

<footer class="footer">
  <p class="copy">Copyright © 2017 Maison Lumen Apartments Prague. All Rights Reserved.</p>
  <div class="social" aria-label="Social links"><span></span><span></span><span></span><span></span></div>
</footer>
<div class="message">
  <span class="round-icon" style="background:#fff"><svg width="16" height="12" viewBox="0 0 16 12"><rect x="0.5" y="0.5" width="15" height="11" fill="none" stroke="#b5a28b"/><path d="M1 1l7 6 7-6" fill="none" stroke="#b5a28b"/></svg></span>
  Please leave a message
</div>

</body>
</html>
```